Business Card for a mobile physiotherapy company

I need a layout for a business card for a mobile physiotherapy company.
Slogan is "Mobile Physiotherapy - Your Road To Recovery"
Phone number is 867-555-0142
Email VardenTherapy@postnest.ca (subject to change with website)
Website www.VardenTherapy.ca
My name and credentials: Luke Varden Luke Varden, BSc(kin), MPT, CAFCI, IMS
Information maybe included: Direct Billing, Services including Physiotherapy, IMS, acupuncture
Maybe include facebook and instagram logos
One side with the logo clean and sharp
Other side with details, try not to look too busy, keep everything concise

```html
<!DOCTYPE html>
<html lang="en">
<head>
<meta charset="utf-8">
<title>Varden Therapy – Business Card</title>
<link rel="stylesheet" href="https://fonts.googleapis.com/css2?family=Roboto:wght@400;500;700&display=swap">
<style>
  :root {
    --bg: #e6e6e8;
    --teal-deep: #145a4e;
    --teal: #1f6b66;
    --navy-blue: #2b4f7e;
    --brand-blue: #4a6a98;
    --brand-teal: #1d6e62;
    --ink: #233238;
    --paper: #ffffff;
    --rule: #4a6a98;
  }
  * { box-sizing: border-box; margin: 0; padding: 0; }
  html, body { width: 1200px; height: 900px; overflow: hidden; }
  body {
    background: var(--bg);
    font-family: "Roboto", Arial, sans-serif;
    display: flex;
    flex-direction: column;
    align-items: center;
    justify-content: center;
    gap: 40px;
  }
  .card {
    width: 700px;
    height: 400px;
    position: relative;
    overflow: hidden;
    box-shadow: 0 6px 18px rgba(0,0,0,0.18);
    background: var(--paper);
  }

  /* Front side */
  .card-front .front-field {
    position: absolute;
    inset: 0 0 52px 0;
    background: linear-gradient(30deg, var(--teal-deep) 0%, var(--teal) 45%, var(--navy-blue) 100%);
    display: flex;
    flex-direction: column;
    align-items: center;
    justify-content: center;
    gap: 34px;
    color: var(--paper);
  }
  .brand-name {
    display: flex;
    align-items: center;
    gap: 14px;
    font-size: 46px;
    font-weight: 700;
    letter-spacing: 3px;
    text-transform: uppercase;
  }
  .brand-dot {
    width: 16px; height: 16px;
    border-radius: 50%;
    background: currentColor;
  }
  .services {
    display: flex;
    align-items: center;
    gap: 26px;
    font-size: 19px;
    font-weight: 400;
    letter-spacing: 0.5px;
  }
  .services .sep {
    width: 9px; height: 9px; border-radius: 50%; background: var(--paper);
  }
  .slogan-band {
    position: absolute;
    left: 0; right: 0; bottom: 0;
    height: 52px;
    display: flex;
    align-items: center;
    justify-content: center;
    font-size: 18px;
    color: var(--ink);
    letter-spacing: 0.3px;
  }

  /* Back side */
  .card-back .brand-name {
    position: absolute;
    top: 78px;
    left: 0; right: 0;
    justify-content: center;
    color: var(--brand-teal);
  }
  .back-details {
    position: absolute;
    top: 190px;
    left: 0; right: 0;
    display: flex;
    align-items: center;
    justify-content: center;
    gap: 30px;
  }
  .person { text-align: right; }
  .person-name {
    font-size: 30px;
    font-weight: 700;
    color: var(--brand-blue);
    margin-bottom: 6px;
  }
  .person-credentials {
    font-size: 19px;
    color: var(--ink);
  }
  .divider {
    width: 2px;
    height: 120px;
    background: var(--rule);
  }
  .contact-list { list-style: none; display: flex; flex-direction: column; gap: 10px; }
  .contact-item {
    display: flex; align-items: center; gap: 12px;
    font-size: 18px; color: var(--ink);
  }
  .contact-icon {
    width: 28px; height: 28px;
    background: var(--brand-blue);
    display: flex; align-items: center; justify-content: center;
    flex: none;
  }
</style>
</head>
<body>

  <section class="card card-front" aria-label="Business card front">
    <div class="front-field">
      <div class="brand-name"><span class="brand-dot"></span>Varden Therapy</div>
      <div class="services">
        <span>Physiotherapy</span><span class="sep"></span>
        <span>IMS</span><span class="sep"></span>
        <span>Acupuncture</span>
      </div>
    </div>
    <div class="slogan-band">Mobile Physiotherapy - Your Road To Recovery</div>
  </section>

  <section class="card card-back" aria-label="Business card back">
    <div class="brand-name"><span class="brand-dot"></span>Varden Therapy</div>
    <div class="back-details">
      <div class="person">
        <div class="person-name">Luke Varden</div>
        <div class="person-credentials">BSc(kin), MPT, CAFCI, IMS</div>
      </div>
      <div class="divider"></div>
      <ul class="contact-list">
        <li class="contact-item">
          <span class="contact-icon">
            <svg width="16" height="16" viewBox="0 0 24 24" fill="#fff"><path d="M6.6 10.8a15.1 15.1 0 0 0 6.6 6.6l2.2-2.2a1 1 0 0 1 1-.25 11.4 11.4 0 0 0 3.6.57 1 1 0 0 1 1 1V20a1 1 0 0 1-1 1A17 17 0 0 1 3 4a1 1 0 0 1 1-1h3.5a1 1 0 0 1 1 1c0 1.25.2 2.45.57 3.57a1 1 0 0 1-.25 1z"/></svg>
          </span>867-555-0142
        </li>
        <li class="contact-item">
          <span class="contact-icon">
            <svg width="16" height="16" viewBox="0 0 24 24" fill="none" stroke="#fff" stroke-width="2"><rect x="3" y="5" width="18" height="14"/><path d="M3 6l9 7 9-7"/></svg>
          </span>VardenTherapy@postnest.ca
        </li>
        <li class="contact-item">
          <span class="contact-icon">
            <svg width="16" height="16" viewBox="0 0 24 24" fill="none" stroke="#fff" stroke-width="1.8"><circle cx="12" cy="12" r="9"/><path d="M3 12h18M12 3c3 3 3 15 0 18M12 3c-3 3-3 15 0 18"/></svg>
          </span>www.VardenTherapy.ca
        </li>
      </ul>
    </div>
  </section>

</body>
</html>
```